BildeVOLD buisnesscard

Hey :) I need a modern buisnesscard for my company BildeVOLD
It most have:
Dagligleder og Fotograf: Henrik Audun Strandvik

Mob: +4791264085
Epost: post@bildevold.example
Adresse: Kvernbakken9, 6040 Fjordvik

Facbook and instagram logo with text BildeVOLD

BildeVOLD logo

It Company

```html
<!DOCTYPE html>
<html lang="no">
<head>
<meta charset="utf-8">
<title>BildeVOLD – visittkort</title>
<link rel="stylesheet" href="https://fonts.googleapis.com/css2?family=Montserrat:wght@400;600;700;800&display=swap">
<style>
  :root {
    --bg: #d9d9d9;
    --blue: #1f7fb3;
    --pink: #c93f8a;
    --white: #eeeeee;
    --dark: #232323;
    --text-light: #ffffff;
    --line-grey: #8a8a8a;
  }
  * { box-sizing: border-box; margin: 0; padding: 0; }
  html, body {
    width: 1200px;
    height: 799px;
    overflow: hidden;
    background: var(--bg);
    font-family: "Montserrat", Arial, sans-serif;
  }
  .stage {
    position: relative;
    width: 1200px;
    height: 799px;
  }
  .card {
    position: absolute;
    top: 100px;
    width: 350px;
    height: 600px;
    overflow: hidden;
    box-shadow: 0 10px 30px rgba(0,0,0,0.25);
  }
  .card--front { left: 215px; background: var(--white); }
  .card--back  { left: 635px; background: var(--dark); }

  .front-bands {
    position: absolute;
    inset: 0;
    width: 350px;
    height: 600px;
  }
  .contact-head {
    position: absolute;
    top: 38px;
    left: 20px;
    right: 24px;
    text-align: right;
    color: var(--text-light);
  }
  .contact-name {
    font-weight: 700;
    font-size: 17px;
    letter-spacing: 0.3px;
    text-transform: uppercase;
    line-height: 22px;
  }
  .contact-role {
    font-weight: 700;
    font-size: 14px;
    line-height: 20px;
  }
  .contact-list {
    position: absolute;
    top: 112px;
    left: 20px;
    right: 24px;
    list-style: none;
    text-align: right;
    color: var(--text-light);
    font-size: 13px;
    line-height: 21px;
  }
  .contact-list .gap { margin-top: 12px; }
  .contact-list strong { font-weight: 700; }

  .wordmark {
    font-weight: 800;
    color: var(--blue);
    letter-spacing: 0.5px;
  }
  .wordmark--front {
    position: absolute;
    left: 0;
    right: 0;
    top: 470px;
    text-align: center;
    font-size: 44px;
  }
  .wordmark--back {
    position: absolute;
    left: 0;
    right: 0;
    top: 225px;
    text-align: center;
    font-size: 42px;
  }
  .social-row {
    position: absolute;
    top: 300px;
    left: 0;
    right: 0;
    display: flex;
    align-items: center;
    justify-content: center;
    gap: 10px;
  }
  .social-row .rule {
    width: 80px;
    height: 1px;
    background: var(--line-grey);
  }
  .social-row .dot {
    width: 20px;
    height: 20px;
    border-radius: 50%;
    background: var(--pink);
  }
  .social-row .handle {
    color: var(--pink);
    font-weight: 600;
    font-size: 13px;
  }
</style>
</head>
<body>
<main class="stage">
  <section class="card card--front" aria-label="Visittkort forside">
    <svg class="front-bands" viewBox="0 0 350 600" aria-hidden="true">
      <polygon points="0,0 350,0 350,368 0,278" fill="var(--blue)"/>
      <polygon points="0,283 350,373 350,381 0,291" fill="var(--pink)"/>
    </svg>
    <header class="contact-head">
      <h1 class="contact-name">Henrik Audun Strandvik</h1>
      <p class="contact-role">Dagligleder og Fotograf</p>
    </header>
    <ul class="contact-list">
      <li>Kvernbakken9</li>
      <li>6040 Fjordvik</li>
      <li class="gap">+4791264085</li>
      <li>post@bildevold.example</li>
      <li class="gap">www.<strong>bildevold</strong>.example</li>
    </ul>
    <p class="wordmark wordmark--front">BildeVOLD</p>
  </section>

  <section class="card card--back" aria-label="Visittkort bakside">
    <p class="wordmark wordmark--back">BildeVOLD</p>
    <div class="social-row">
      <span class="rule"></span>
      <span class="dot"></span>
      <span class="handle">BildeVOLD</span>
      <span class="rule"></span>
    </div>
  </section>
</main>
</body>
</html>
```